Wordpress Design Project for Bankruptcy Law Office in San Francisco

our current website: www.dorvanelilaw-example.com

we would like to re-design it for wordpress to make it faster and a bit more modern.

content should be similar to what we have there right now but also we do family law

please include logo for law office:

Law Office of Marta K. Dolvenidze

Thank you.
Updates

please see attached word document with logos that we like as an example.

we do tend to like color red.  darker red.

Please submit your design variations and logo as soon as possible.   We would like to go over them and make our decision

Reason: Please create couple of more variations of logo for your design, so we can make our decision what we like the most. Please see word doc for samples: Text: Law Office Of Marta K. Dolvenidze

Reason: final touches

Target Market(s)

bankruptcy and family law clients

Industry/Entity Type

Family Law

Requirements
Must have
• see examples of law sites
http://promo.lexorbin-example.com/testimonials

- new logo: Law Office of Marta K. Dolvenidze
- client intake form
- blog
- contact us form

Nice to have
• - map
- red color
- on the front page a nice photo of SF or a happy family

```html
<!DOCTYPE html>
<html lang="en">
<head>
<meta charset="utf-8">
<title>Law Office of Marta K. Dolvenidze</title>
<link href="https://fonts.googleapis.com/css2?family=Cinzel:wght@400;600&family=Source+Sans+3:ital,wght@0,400;0,600;1,400&display=swap" rel="stylesheet">
<style>
:root{
  --red:#b5100b;
  --red-dark:#960808;
  --yellow:#f6d43b;
  --text:#4a4a4a;
  --bg:#f4f4f4;
  --panel:#fff;
  --line:#c8c8c8;
}
*{box-sizing:border-box;margin:0;padding:0}
html,body{width:821px;height:1200px;overflow:hidden}
body{position:relative;background:var(--bg);font-family:"Source Sans 3",sans-serif;color:var(--text)}
.abs{position:absolute}
.top-rule{left:0;top:0;width:821px;height:5px;background:var(--red)}
.brand-mark{left:72px;top:6px;width:50px;height:50px;background:var(--red)}
.brand-name{left:130px;top:18px;font-family:"Cinzel",serif;font-size:19px;line-height:23px;color:var(--red);letter-spacing:1px}
.brand-name span{display:block}
.search{left:636px;top:38px;width:134px;height:18px;border:1px solid #ccc;background:#fff;font-size:8px;color:#aaa;padding:3px 10px;font-style:italic}
.search svg{position:absolute;right:5px;top:4px}
.nav-band{left:0;top:94px;width:821px;height:20px;background:var(--red)}
.nav{left:51px;top:86px;width:720px;height:36px;background:linear-gradient(#c8160f,#9c0b07);display:flex;border-radius:2px}
.nav a{color:#fff;text-decoration:none;font-size:10px;display:flex;align-items:center;justify-content:center;border-right:1px solid rgba(0,0,0,.25)}
.nav a:last-child{border-right:0}
.nav a.active{background:rgba(255,255,255,.08)}
.hero{left:51px;top:128px;width:720px;height:224px;border:2px solid #ddd;background:
  linear-gradient(180deg,rgba(0,0,0,0) 72%,rgba(120,80,55,.35) 80%,rgba(150,100,70,.55) 100%),
  radial-gradient(ellipse 32% 55% at 64% 48%,#6a4630 0%,rgba(106,70,48,.55) 45%,rgba(106,70,48,0) 75%),
  linear-gradient(100deg,#ece6e8 0%,#ddd2d5 40%,#b8a6a4 70%,#7a6a64 100%)}
.hero h1{position:absolute;left:51px;top:57px;font-weight:400;font-size:22px;color:#3a3030}
.dots{position:absolute;left:20px;top:197px;display:flex;gap:8px}
.dots i{width:8px;height:8px;border-radius:50%;background:#333}
.dots i:first-child{background:var(--red)}
.panel{left:50px;top:360px;width:721px;height:760px;background:var(--panel)}
h2{position:absolute;font-weight:400;font-size:15px;color:var(--red)}
.welcome-text{left:64px;top:409px;width:493px;font-size:9px;line-height:16.4px;text-align:justify}
.checks{font-size:9px;list-style:none}
.checks li{height:19.4px;padding-left:18px;position:relative}
.checks li svg{position:absolute;left:0;top:2px}
.hr{height:1px;background:var(--line)}
.dotted{border-top:1px dotted #999;height:0}
.news-icon{width:24px;height:24px;border-radius:50%;background:#ddd;display:flex;align-items:center;justify-content:center}
.small{font-size:8.5px;line-height:13.5px}
.date{color:var(--red);font-style:italic}
.story-title{font-size:10px;font-weight:600;color:var(--red)}
.more{width:44px;height:19px;background:var(--red-dark);color:#fff;font-size:8.5px;font-weight:600;border-radius:2px;display:flex;align-items:center;justify-content:center}
.form{left:539px;top:781px;width:217px;height:319px;background:var(--red-dark)}
.form-tab{left:105px;top:1px;width:112px;height:24px;background:linear-gradient(#f8e46a,var(--yellow));color:var(--red);font-size:12px;display:flex;align-items:center;justify-content:center}
.form-title{left:6px;top:6px;color:#fff;font-size:12px}
.form label{position:absolute;left:15px;color:#fff;font-size:8.5px;font-weight:400}
.field{position:absolute;left:13px;width:194px;height:18px;background:#fff}
.btn{position:absolute;height:19px;background:#6e0504;color:#fff;font-size:8.5px;font-weight:600;display:flex;align-items:center;justify-content:center}
.footer-links{left:50px;top:1135px;font-size:8.5px;color:#555}
.footer-links span{margin:0 5px;color:#888}
.copy{left:50px;top:1153px;font-size:8.5px;color:#555}
.social{width:22px;height:22px;border-radius:50%;background:#a9a9a9}
</style>
</head>
<body>
<div class="abs top-rule"></div>
<div class="abs brand-mark"></div>
<div class="abs brand-name"><span>Law Office of</span><span>Marta K. Dolvenidze</span></div>
<div class="abs search">Search<svg width="8" height="8" viewBox="0 0 8 8"><circle cx="3.2" cy="3.2" r="2.4" fill="none" stroke="#aaa"/><path d="M5 5l2.5 2.5" stroke="#aaa"/></svg></div>

<div class="abs nav-band"></div>
<nav class="abs nav">
  <a class="active" style="width:75px">HOME</a>
  <a style="width:84px">ABOUT US</a>
  <a style="width:80px">LAWYERS</a>
  <a style="width:97px">LATEST NEWS</a>
  <a style="width:113px">LATEST ARTICLES</a>
  <a style="width:111px">PRACTICE AREAS</a>
  <a style="width:96px">CONTACT US</a>
  <a style="width:64px">FAQ</a>
</nav>

<section class="abs hero" role="img" aria-label="Wooden judge's gavel resting on its sound block on a polished table">
  <h1>DUIS AUTE IRURE DOLOR</h1>
  <div class="dots"><i></i><i></i><i></i><i></i></div>
</section>

<div class="abs panel"></div>
<h2 style="left:64px;top:378px">WELCOME TO OUR SITE</h2>
<p class="abs welcome-text">Sed ut perspiciatis unde omnis iste natus error sit voluptatem accusantium doloremque laudantium, totam rem aperiam, eaque ipsa quae ab illo inventore veritatis et quasi architecto beatae vitae dicta sunt explicabo. Nemo enim ipsam voluptatem quia voluptas sit aspernatur aut odit aut fugit, sed quia consequuntur magni dolores eos qui ratione voluptatem sequi nesciunt. Neque porro quisquam est, qui dolorem ipsum quia dolor sit amet, consectetur, adipisci velit, sed quia non numquam eius modi tempora incidunt ut labore et dolore magnam aliquam.</p>
<ul class="abs checks" style="left:88px;top:504px">
  <li><svg width="8" height="8" viewBox="0 0 8 8"><circle cx="4" cy="4" r="3.3" fill="none" stroke="#555" stroke-width="1.2"/><path d="M3.3 2.4L5 4 3.3 5.6" fill="none" stroke="#555" stroke-width="1.1"/></svg>Duis accumsan aliquet arcu, vitae</li>
  <li><svg width="8" height="8" viewBox="0 0 8 8"><circle cx="4" cy="4" r="3.3" fill="none" stroke="#555" stroke-width="1.2"/><path d="M3.3 2.4L5 4 3.3 5.6" fill="none" stroke="#555" stroke-width="1.1"/></svg>Morbi non lacus scelerisque nisl rhoncus</li>
  <li><svg width="8" height="8" viewBox="0 0 8 8"><circle cx="4" cy="4" r="3.3" fill="none" stroke="#555" stroke-width="1.2"/><path d="M3.3 2.4L5 4 3.3 5.6" fill="none" stroke="#555" stroke-width="1.1"/></svg>Pellentesque pellentesque</li>
  <li><svg width="8" height="8" viewBox="0 0 8 8"><circle cx="4" cy="4" r="3.3" fill="none" stroke="#555" stroke-width="1.2"/><path d="M3.3 2.4L5 4 3.3 5.6" fill="none" stroke="#555" stroke-width="1.1"/></svg>Cras venenatis massa ut orci pretium sit</li>
</ul>
<ul class="abs checks" style="left:312px;top:504px">
  <li><svg width="8" height="8" viewBox="0 0 8 8"><circle cx="4" cy="4" r="3.3" fill="none" stroke="#555" stroke-width="1.2"/><path d="M3.3 2.4L5 4 3.3 5.6" fill="none" stroke="#555" stroke-width="1.1"/></svg>Duis accumsan aliquet arcu, vitae</li>
  <li><svg width="8" height="8" viewBox="0 0 8 8"><circle cx="4" cy="4" r="3.3" fill="none" stroke="#555" stroke-width="1.2"/><path d="M3.3 2.4L5 4 3.3 5.6" fill="none" stroke="#555" stroke-width="1.1"/></svg>Morbi non lacus scelerisque nisl rhoncus</li>
  <li><svg width="8" height="8" viewBox="0 0 8 8"><circle cx="4" cy="4" r="3.3" fill="none" stroke="#555" stroke-width="1.2"/><path d="M3.3 2.4L5 4 3.3 5.6" fill="none" stroke="#555" stroke-width="1.1"/></svg>Pellentesque pellentesque</li>
  <li><svg width="8" height="8" viewBox="0 0 8 8"><circle cx="4" cy="4" r="3.3" fill="none" stroke="#555" stroke-width="1.2"/><path d="M3.3 2.4L5 4 3.3 5.6" fill="none" stroke="#555" stroke-width="1.1"/></svg>Cras venenatis massa ut orci pretium sit</li>
</ul>
<div class="abs" style="left:566px;top:404px;width:186px;height:152px;background:radial-gradient(ellipse 48% 40% at 50% 55%,#c8282a 0%,rgba(200,40,42,.5) 50%,rgba(255,255,255,0) 100%),linear-gradient(180deg,#fff 0%,#f3ece8 100%)" role="img" aria-label="Happy family of parents and three children sitting together"></div>

<div class="abs hr" style="left:64px;top:595px;width:693px"></div>

<h2 style="left:64px;top:612px;font-size:13px">LATEST NEWS</h2>
<h2 style="left:438px;top:612px;font-size:13px">ABOUT US</h2>
<div class="abs dotted" style="left:64px;top:643px;width:348px"></div>
<div class="abs dotted" style="left:438px;top:643px;width:317px"></div>

<div class="abs news-icon" style="left:66px;top:662px"><svg width="12" height="12" viewBox="0 0 12 12"><rect x="1" y="1" width="8" height="8" fill="none" stroke="#fff" stroke-width="1.3"/><rect x="3.5" y="3.5" width="7.5" height="7.5" fill="none" stroke="#fff" stroke-width="1.3"/></svg></div>
<p class="abs small" style="left:102px;top:659px;width:310px;text-align:justify">Sed ut perspiciatis unde omnis iste natus error sit voluptatem accusantium doloremque laudantium, totam rem aperiam, eaque ipsa quae ab illo inventore veritatis<br><span class="date">August 29th, 2012</span></p>
<div class="abs news-icon" style="left:66px;top:715px"><svg width="12" height="12" viewBox="0 0 12 12"><rect x="1" y="1" width="8" height="8" fill="none" stroke="#fff" stroke-width="1.3"/><rect x="3.5" y="3.5" width="7.5" height="7.5" fill="none" stroke="#fff" stroke-width="1.3"/></svg></div>
<p class="abs small" style="left:102px;top:712px;width:310px;text-align:justify">Sed ut perspiciatis unde omnis iste natus error sit voluptatem accusantium doloremque laudantium, totam rem aperiam, eaque ipsa quae ab illo inventore veritatis<br><span class="date">August 29th, 2012</span></p>

<p class="abs small" style="left:438px;top:659px;width:190px">Sed ut perspiciatis unde omnis iste natus error sit voluptatem accusantium dolor emque laudantium, totam rem aperiam, eaque ipsa quae ab illo inven- voluptatum deleniti atque corrupti quos dolores et quas molestias excepturi sint occaecati cupiditate<br><span class="date">View more</span></p>
<div class="abs" style="left:641px;top:660px;width:116px;height:77px;background:radial-gradient(ellipse 30% 55% at 50% 55%,#6a4a2a 0%,rgba(106,74,42,0) 100%),linear-gradient(135deg,#f2e6cf,#cfae7c)" role="img" aria-label="Bronze statue of Lady Justice holding scales"></div>

<div class="abs hr" style="left:64px;top:766px;width:693px"></div>

<h2 style="left:65px;top:776px;font-size:13px">FAMILY LAW</h2>
<div class="abs" style="left:65px;top:804px;width:163px;height:108px;background:linear-gradient(180deg,#f6efe6 0%,#f2c65a 45%,#e9b84a 80%,#f4f4f4 100%)" role="img" aria-label="Smiling family lying together on a bed"></div>
<div class="abs story-title" style="left:238px;top:804px">Story Tittle line goes here</div>
<p class="abs small" style="left:238px;top:821px;width:258px">Lorem ipsum dolor sit amet, consectetuer adipiscing elit. Nam cursus. Morbi ut mi. Nullam enim leo, egestas id, condimentum at, laoreet mattis, massa.</p>
<p class="abs small" style="left:238px;top:865px;width:258px">Sed eleifend nonummy diam. Praesent mauris ante, elementum et, bibendum at, posuere sit amet, nibh. Duis tincidunt lectus quis dui viverra vestibulum.</p>
<div class="abs more" style="left:434px;top:899px">More..</div>

<h2 style="left:65px;top:926px;font-size:13px">BANKRUPTCY..</h2>
<div class="abs" style="left:65px;top:954px;width:163px;height:108px;background:linear-gradient(180deg,#4a2a20 0%,#6a3e28 45%,#8a5232 75%,#5a3220 100%)" role="img" aria-label="Gavel in front of leather law books"></div>
<div class="abs story-title" style="left:241px;top:959px">Story Tittle line goes here</div>
<p class="abs small" style="left:241px;top:976px;width:258px">Lorem ipsum dolor sit amet, consectetuer adipiscing elit. Nam cursus. Morbi ut mi. Nullam enim leo, egestas id, condimentum at, laoreet mattis, massa.</p>
<p class="abs small" style="left:241px;top:1020px;width:258px">Sed eleifend nonummy diam. Praesent mauris ante, elementum et, bibendum at, posuere sit amet, nibh. Duis tincidunt lectus quis dui viverra vestibulum.</p>
<div class="abs more" style="left:434px;top:1057px">More..</div>

<form class="abs form">
  <div class="abs form-title">CONTACT FORM</div>
  <div class="abs form-tab">CLIENT FORM</div>
  <label style="top:34px">Name:</label><div class="field" style="top:49px"></div>
  <label style="top:70px">Email:</label><div class="field" style="top:86px"></div>
  <label style="top:107px">Phone:</label><div class="field" style="top:122px"></div>
  <label style="top:142px">Subject:</label><div class="field" style="top:158px"></div>
  <label style="top:179px">Message:</label><div class="field" style="top:195px;height:50px"></div>
  <div class="abs" style="left:15px;top:256px;width:8px;height:8px;background:#fff"></div>
  <label style="left:29px;top:253px;font-size:7.5px">Send a copy of this message to yourself</label>
  <div class="btn" style="left:15px;top:275px;width:44px">SEND</div>
  <div class="btn" style="left:69px;top:275px;width:43px">RESET</div>
</form>

<div class="abs footer-links">Home<span>|</span>About us<span>|</span>Lawyers<span>|</span>Latest News<span>|</span>Latest Articles<span>|</span>Practice Areas<span>|</span>Contact us<span>|</span>FAQ</div>
<div class="abs copy">Copyright © 2012 www.dorvanelilaw-example.com &nbsp;&nbsp; All rights reserved.</div>
<div class="abs social" style="left:708px;top:1139px"></div>
<div class="abs social" style="left:740px;top:1139px"></div>
</body>
</html>
```